Web Developer Needs a Business Card Design

I need a personal business card design that represents me as a web developer for potential employers. I would like the background to be a dark color on the front for contrast with my logo and name. The back will have all my information along with a smaller version of the logo. I want something with a modern look and feel, not too conservative. This will be used for potential employers and freelance work.

Industry/Entity Type

Business

Contact Information for Business Card

Front should have my logo and name. The back should have all my personal information which would include: name: Tom Varulek, phone: 570-614-3098, email: tomvarulek@quillbox.net, website url: www.tomvarulek.net, logo, web developer.

Font styles to use
Sans Serif

Requirements
Must have
• Must include my logo. The color palette base color will be the logo color.

```html
<!DOCTYPE html>
<html lang="en">
<head>
<meta charset="utf-8">
<title>Tom Varulek — Business Card</title>
<link rel="stylesheet" href="https://fonts.googleapis.com/css2?family=Open+Sans:wght@400;600&display=swap">
<style>
  :root {
    --backdrop: #2b2724;
    --card: #050505;
    --teal: #63c5b0;
    --white: #ffffff;
    --soft-white: #e9e9e9;
  }
  * { box-sizing: border-box; margin: 0; padding: 0; }
  html, body {
    width: 1200px;
    height: 780px;
    overflow: hidden;
    background: var(--backdrop);
    font-family: "Open Sans", sans-serif;
  }
  .canvas {
    position: relative;
    width: 1200px;
    height: 780px;
  }
  .card {
    position: absolute;
    top: 236px;
    width: 540px;
    height: 309px;
    background: var(--card);
    box-shadow: 0 10px 28px rgba(0,0,0,0.55);
  }
  .card--back { left: 40px; }
  .card--front { left: 620px; }
  .card__frame {
    position: absolute;
    inset: 16px;
    border: 1.5px solid var(--teal);
  }
  .mark {
    position: absolute;
    left: 50%;
    transform: translateX(-50%);
    display: flex;
    align-items: center;
    gap: 10px;
    color: var(--teal);
    font-weight: 600;
    white-space: nowrap;
  }
  .mark__ring {
    display: block;
    border: 5px solid var(--teal);
    border-radius: 50%;
  }
  .card--back .mark { top: 40px; font-size: 20px; }
  .card--back .mark__ring { width: 46px; height: 46px; border-width: 4px; }
  .card--front .mark { top: 62px; font-size: 28px; }
  .card--front .mark__ring { width: 92px; height: 92px; border-width: 6px; }

  .identity {
    position: absolute;
    top: 160px;
    right: 282px;
    text-align: right;
    color: var(--white);
  }
  .identity__name { font-size: 21px; font-weight: 400; line-height: 1.15; }
  .identity__role { font-size: 15px; color: var(--soft-white); line-height: 1.2; }
  .divider {
    position: absolute;
    left: 270px;
    top: 150px;
    width: 1.5px;
    height: 72px;
    background: var(--white);
  }
  .contacts {
    position: absolute;
    left: 286px;
    top: 156px;
    list-style: none;
    color: var(--white);
    font-size: 14px;
    line-height: 21px;
  }
  .contacts li { display: flex; align-items: center; gap: 7px; }
  .contacts svg { width: 12px; height: 12px; flex: none; }

  .front-name {
    position: absolute;
    left: 0;
    right: 0;
    top: 196px;
    text-align: center;
    color: var(--white);
    font-size: 36px;
    font-weight: 400;
    letter-spacing: 0.5px;
  }
</style>
</head>
<body>
<main class="canvas">

  <section class="card card--back" aria-label="Card back with contact details">
    <div class="card__frame"></div>
    <div class="mark"><span class="mark__ring"></span>Tom Varulek</div>
    <div class="identity">
      <p class="identity__name">Tom Varulek</p>
      <p class="identity__role">web developer</p>
    </div>
    <div class="divider"></div>
    <ul class="contacts">
      <li>
        <svg viewBox="0 0 12 12" aria-hidden="true"><rect width="12" height="12" rx="2" fill="#fff"/><path d="M3.5 2.5l1.5 1.6-.8 1.2c.5 1 1.3 1.8 2.3 2.3l1.2-.8 1.6 1.5-.9 1.2C5.8 9.3 2.7 6.2 2.4 3.4z" fill="#050505"/></svg>
        570-614-3098
      </li>
      <li>
        <svg viewBox="0 0 12 12" aria-hidden="true"><rect width="12" height="12" rx="2" fill="#fff"/><rect x="2.5" y="3.5" width="7" height="5" fill="none" stroke="#050505" stroke-width="1"/><path d="M2.5 3.5L6 6.3 9.5 3.5" fill="none" stroke="#050505" stroke-width="1"/></svg>
        tomvarulek@quillbox.net
      </li>
      <li>
        <svg viewBox="0 0 12 12" aria-hidden="true"><rect width="12" height="12" rx="2" fill="#fff"/><circle cx="6" cy="6" r="3.4" fill="none" stroke="#050505" stroke-width="1"/><path d="M2.6 6h6.8M6 2.6c-1.6 2-1.6 4.8 0 6.8M6 2.6c1.6 2 1.6 4.8 0 6.8" fill="none" stroke="#050505" stroke-width=".8"/></svg>
        www.tomvarulek.net
      </li>
    </ul>
  </section>

  <section class="card card--front" aria-label="Card front">
    <div class="card__frame"></div>
    <div class="mark"><span class="mark__ring"></span></div>
    <p class="front-name">Tom Varulek</p>
  </section>

</main>
</body>
</html>
```